Velan Tea Label & packaging for a premium tea brand. For local and global market

Create a look and feel for a box and rectangle tin. We are looking for a luxe packaging design for a new tea brand based in Kenya called 'Velan Tea'. Kenya is home to the finest teas in the world and Velan tea looks to embody that fact. Velan Tea uses the most premium of Kenyan Tea, Black tea, Purple tea, White Tea, Green tea, Hibiscus Tea and Moringa Tea. Velan Tea is handpicked from Kenya's highlands. This project will include the look and feel of the different teas described above. The copy on the main face of the box should read 'Premium Kenyan Tea' The box will contain 25 tagged tea bags, with a net weight of 50 gms.

On one side of the box will read 'packaging instructions' To fully savour this Velan premium tea, use one tea bag for each cup, add some freshly bolded water and wait for 2 minutes as you enjoy the sweet aroma of our tea, stir and serve' Ingredients : Black Tea, and for the others the same : Hibiscus Tea, Green Tea, Purple Tea, White tea. should also feature on the label: Produce of Kenya.

Target Market(s)

Premium

Industry/Entity Type

Agribusiness

Font styles to use
Script

Colors

Designer to choose colors to be used in the design.

Requirements
Must have
• Luxe look and feel
Nice to have
• I have attached the Velan tea logo and images of brands I'd lile the designer to be inspired by.
Should not have
• Green and yellow colours

```html
<!DOCTYPE html>
<html lang="en">
<head>
<meta charset="UTF-8">
<title>Velan Hibiscus Tea – Box Panels</title>
<link href="https://fonts.googleapis.com/css2?family=Libre+Baskerville:ital,wght@0,400;0,700;1,400&family=Lora:ital,wght@0,400;1,400&family=Oswald:wght@400;500&display=swap" rel="stylesheet">
<style>
  :root {
    --backdrop: #e4e2e2;
    --box-black: #262626;
    --box-black-deep: #1c1c1c;
    --label-red: #c9432f;
    --copper: #d98a4f;
    --copper-soft: #e79a69;
    --cream: #f4efe9;
    --pattern-slate: #6f7f86;
    --pattern-slate-dark: #45525a;
    --rule-grey: #8a8a8a;
  }
  * { margin: 0; padding: 0; box-sizing: border-box; }
  html, body { width: 1200px; height: 974px; overflow: hidden; }
  body { background: var(--backdrop); position: relative; }

  .panel { position: absolute; background: var(--box-black); }

  /* Top lid */
  .lid { left: 80px; top: 40px; width: 560px; height: 160px; background: var(--box-black-deep);
         display: flex; align-items: center; justify-content: center; }
  .lid-brand { font-family: "Libre Baskerville", serif; font-size: 44px; letter-spacing: 10px;
               color: var(--copper); font-weight: 400; }

  /* Front face */
  .front { left: 80px; top: 210px; width: 560px; height: 560px; overflow: hidden; }
  .pattern-band { position: absolute; left: 0; bottom: 0; width: 100%; height: 230px;
    background: linear-gradient(180deg, var(--pattern-slate-dark), var(--pattern-slate) 55%, var(--pattern-slate-dark)); opacity: .85; }
  .label-frame { position: absolute; left: 120px; top: 80px; width: 320px; height: 320px;
    background: var(--box-black-deep); border: 3px solid var(--copper); padding: 16px; }
  .label { width: 100%; height: 100%; background: var(--label-red); outline: 1px solid var(--box-black);
    display: flex; flex-direction: column; align-items: center; justify-content: center; text-align: center; }
  .label-brand { font-family: "Libre Baskerville", serif; font-size: 54px; color: var(--copper-soft);
    letter-spacing: 3px; line-height: 1; }
  .label-product { font-family: "Libre Baskerville", serif; font-size: 23px; color: var(--cream);
    letter-spacing: 1px; margin-top: 8px; }
  .label-tagline { font-family: "Lora", serif; font-style: italic; font-size: 21px; color: var(--copper-soft);
    margin-top: 6px; }
  .label-count { font-family: "Oswald", sans-serif; font-size: 14px; color: var(--cream);
    letter-spacing: 1.5px; margin-top: 30px; }

  /* Side face */
  .side { left: 660px; top: 210px; width: 460px; height: 560px; }
  .instructions { position: absolute; left: 50px; top: 120px; width: 360px; height: 330px;
    border: 1px solid var(--rule-grey); padding: 58px 34px 0; text-align: center; }
  .instructions-title { position: absolute; left: 50%; top: -24px; transform: translateX(-50%);
    background: var(--box-black); padding: 0 10px; font-family: "Libre Baskerville", serif;
    font-size: 15px; line-height: 1.3; color: var(--cream); letter-spacing: .5px; white-space: nowrap; }
  .instructions-copy { font-family: "Lora", serif; font-style: italic; font-size: 17px;
    line-height: 1.5; color: var(--cream); }
  .origin { display: flex; align-items: center; justify-content: center; gap: 8px; margin-top: 22px;
    font-family: "Oswald", sans-serif; font-size: 14px; letter-spacing: 1px; color: var(--cream); }
  .origin-mark { width: 16px; height: 11px; background: var(--label-red); }
</style>
</head>
<body>
  <section class="panel lid">
    <span class="lid-brand">VELAN</span>
  </section>

  <section class="panel front">
    <div class="pattern-band" role="img" aria-label="Decorative slate-blue ornamental tile pattern band"></div>
    <div class="label-frame">
      <div class="label">
        <div class="label-brand">VELAN</div>
        <div class="label-product">HIBISCUS TEA</div>
        <div class="label-tagline">Bold &amp; Uplifting</div>
        <div class="label-count">25 BAGS . 50g</div>
      </div>
    </div>
  </section>

  <section class="panel side">
    <div class="instructions">
      <h2 class="instructions-title">PACKAGING<br>INSTRUCTIONS</h2>
      <p class="instructions-copy">To fully savour this Velan premium tea, use one tea bag for each cup, add some freshly bolded water and wait for 2 minutes as you enjoy the sweet aroma of our tea, stir and serve'<br>Ingredients</p>
      <div class="origin"><span class="origin-mark"></span>PRODUCT OF KENYA</div>
    </div>
  </section>
</body>
</html>
```